New Business Card Design Project

I need a design for business cards, i am an electrical business called "Corvane Electrical and Communications" i need the cards to be double sided with the company logo on the back (attached) the front needs to say my company name, web site, email address, telephone number, and ABN number and electrical license number. I am open to different arrangements of the information but would like the background to be incorporating something electrical or something that looks smart. open to all additional ideas also.

The company colours are orange and grey see logo attached.

Business Name: Corvane Electrical and Communications
Website: corvaneelectricalandcomms.example.com.au
Email: brent@corvaneelectricalandcomms.example.com.au
Telephone(mobile): 0481209736
ABN: 71208349162
Lic No: 418273D

Target Market(s)

Business entities, Project Managers, Accounts, Clients

Industry/Entity Type

Electrician

Contact Information for Business Card

I need a design for business cards, i am an electrical business called "Corvane Electrical and Communications" i need the cards to be double sided with the company logo on the back (attached) the front needs to say my company name

Font styles to use
Serif
Sans Serif

Colors
f37122
5c5c5c

Requirements
Must have
• Must have the Logo on the back open to different ways of it being on the back but had in mind to keep it central but again open to other options
Nice to have
• A real modern cool background that is eye catching yet contemporary
Should not have
• No backgrounds of a light bulb or plug or anything like that

```html
<!DOCTYPE html>
<html lang="en">
<head>
<meta charset="utf-8">
<title>Corvane Electrical and Communications – Business Cards</title>
<link href="https://fonts.googleapis.com/css2?family=Montserrat:wght@600;700&family=Questrial&display=swap" rel="stylesheet">
<style>
  :root {
    --orange: #f7a823;
    --orange-deep: #f37122;
    --grey: #5c5c5c;
    --card-grey: #555658;
    --white: #ffffff;
    --stage: #e9e9e7;
  }
  * { box-sizing: border-box; margin: 0; padding: 0; }
  html, body { width: 1200px; height: 900px; overflow: hidden; }
  body {
    background: var(--stage);
    position: relative;
    font-family: "Questrial", sans-serif;
  }
  .card {
    position: absolute;
    width: 640px;
    height: 366px;
    border-radius: 22px;
    overflow: hidden;
    background: var(--card-grey);
    box-shadow: 0 6px 18px rgba(0,0,0,.18);
  }
  .card-back { left: 80px; top: 70px; }
  .card-front { left: 480px; top: 464px; }

  .brand-name {
    font-family: "Montserrat", sans-serif;
    font-weight: 700;
    color: var(--orange);
    text-transform: uppercase;
    line-height: 1.15;
    display: flex;
    align-items: center;
    gap: 14px;
  }
  .brand-dot {
    width: 18px; height: 18px; border-radius: 50%;
    background: var(--orange); flex: none;
  }

  .card-back .brand-block {
    position: absolute; left: 0; right: 0; top: 118px;
    display: flex; flex-direction: column; align-items: center;
  }
  .card-back .brand-name { font-size: 27px; letter-spacing: .5px; }
  .card-back .brand-name span { display: block; }
  .card-back .back-web {
    margin-top: 18px;
    color: var(--white);
    font-size: 19px;
    letter-spacing: .3px;
  }

  .front-shape { position: absolute; inset: 0; }

  .front-left {
    position: absolute; left: 34px; top: 116px;
  }
  .card-front .brand-name { font-size: 18px; gap: 10px; }
  .card-front .brand-dot { width: 13px; height: 13px; }
  .licence {
    margin-top: 16px;
    font-size: 18px;
    color: var(--orange);
  }
  .licence .licence-number { color: var(--grey); }

  .front-right {
    position: absolute; right: 24px; top: 92px;
    text-align: right;
    color: var(--white);
  }
  .person-name {
    font-size: 23px;
    color: var(--orange);
    text-transform: uppercase;
    letter-spacing: .3px;
    line-height: 1;
  }
  .person-role {
    font-size: 13px;
    text-transform: uppercase;
    letter-spacing: .5px;
    margin-top: 4px;
  }
  .details { margin-top: 10px; list-style: none; font-size: 13px; line-height: 1.5; }
  .details li { display: flex; justify-content: flex-end; align-items: center; gap: 7px; }
  .details .label { color: var(--orange); }
  .details svg { width: 11px; height: 11px; flex: none; }
  .details .icon-space { width: 11px; flex: none; }

  .online {
    position: absolute; right: 24px; bottom: 40px;
    text-align: right; color: var(--white);
    font-size: 12px; line-height: 1.45; list-style: none;
  }
</style>
</head>
<body>

  <section class="card card-back" aria-label="Card back">
    <div class="brand-block">
      <div class="brand-name"><i class="brand-dot"></i><div><span>Corvane Electrical</span><span>and Communications</span></div></div>
      <p class="back-web">www.corvaneelectricalandcomms.example.com.au</p>
    </div>
  </section>

  <section class="card card-front" aria-label="Card front">
    <svg class="front-shape" viewBox="0 0 640 366" width="640" height="366" aria-hidden="true">
      <path d="M0 0 H330 C420 95 385 285 180 366 H0 Z" fill="var(--orange)"/>
      <path d="M0 0 H310 C400 95 365 285 166 366 H0 Z" fill="var(--white)"/>
    </svg>

    <div class="front-left">
      <div class="brand-name"><i class="brand-dot"></i><div>Corvane Electrical<br>and Communications</div></div>
      <p class="licence">Lic No: <span class="licence-number">418273D</span></p>
    </div>

    <div class="front-right">
      <p class="person-name">Tobias Renwick</p>
      <p class="person-role">Director</p>
      <ul class="details">
        <li><span><span class="label">ABN:</span> 71208349162</span><span class="icon-space"></span></li>
        <li>0481 209 736
          <svg viewBox="0 0 12 12"><path d="M2.5 1 L4.5 1 L5.2 3.6 L4 4.6 C4.7 6.2 5.8 7.3 7.4 8 L8.4 6.8 L11 7.5 V9.5 C11 10.3 10.3 11 9.5 11 C5 11 1 7 1 2.5 C1 1.7 1.7 1 2.5 1Z" fill="var(--orange)"/></svg>
        </li>
      </ul>
    </div>

    <ul class="online">
      <li>brent@corvaneelectricalandcomms.example.com.au</li>
      <li>www.corvaneelectricalandcomms.example.com.au</li>
    </ul>
  </section>

</body>
</html>
```